Road Construction Company needs business cards

We would like a new business card designed for our business.

We're a road construction company based in Qld, Australia.

Can the business card please have the following information on it.

Name: Warren Halbeck
Position: General Manager
Phone: 0472 915 348
Email: Warren.halbeck@tovrin.com.au
Address: 87 Marrow Ave, Pendlebay, QLD, 4023
Website: www.tovrin.com.au

Visually we'd like the card to be professional and simple.

Attached is our logo.

Our website is www.tovrin.com.au

Target Market(s)

Men aged 25-60

Contact Information for Business Card

As listed in project description

Font styles to use
Serif

Requirements
Must have
• Large logo on back of card

```html
<!DOCTYPE html>
<html lang="en">
<head>
<meta charset="utf-8">
<title>Tovrin Business Cards</title>
<link href="https://fonts.googleapis.com/css2?family=Lato:wght@400;700;900&display=swap" rel="stylesheet">
<style>
  :root {
    --stage: #2b2b2d;
    --brand-blue: #0a54a3;
    --back-blue: #0b5cae;
    --accent-cyan: #36a3da;
    --logo-cyan: #2cc6ea;
    --logo-navy: #0e4c9c;
    --paper: #ffffff;
    --ink-light: #ffffff;
  }
  html, body {
    margin: 0;
    padding: 0;
    width: 1200px;
    height: 875px;
    overflow: hidden;
    background: var(--stage);
    font-family: "Lato", Arial, sans-serif;
  }
  .canvas {
    width: 1200px;
    height: 875px;
    display: flex;
    align-items: center;
    justify-content: center;
    gap: 44px;
  }
  .card {
    position: relative;
    width: 520px;
    height: 318px;
    overflow: hidden;
    box-shadow: 0 18px 40px rgba(0,0,0,0.45);
  }
  /* Back of card */
  .card-back {
    background: var(--back-blue);
    display: flex;
    align-items: center;
    justify-content: center;
  }
  .card-back .wordmark {
    font-weight: 900;
    font-size: 92px;
    letter-spacing: 2px;
    color: var(--logo-cyan);
    text-transform: uppercase;
  }
  /* Front of card */
  .card-front { background: var(--paper); }
  .card-front .panels {
    position: absolute;
    inset: 0;
    width: 520px;
    height: 318px;
  }
  .panel-blue { fill: var(--brand-blue); }
  .panel-stripe { fill: var(--accent-cyan); }
  .card-front .wordmark {
    position: absolute;
    left: 370px;
    top: 118px;
    width: 135px;
    text-align: center;
    font-weight: 900;
    font-size: 34px;
    letter-spacing: 1px;
    color: var(--logo-navy);
    text-transform: uppercase;
  }
  .contact {
    position: absolute;
    left: 34px;
    top: 110px;
    color: var(--ink-light);
  }
  .contact .name {
    margin: 0;
    font-weight: 900;
    font-size: 25px;
    text-transform: uppercase;
    letter-spacing: 0.2px;
  }
  .contact .role {
    margin: 2px 0 16px;
    font-size: 16px;
    font-weight: 400;
  }
  .details {
    list-style: none;
    margin: 0;
    padding: 0;
    font-size: 13.5px;
    line-height: 1.45;
  }
  .details li {
    display: flex;
    align-items: flex-start;
    gap: 9px;
  }
  .details svg {
    width: 12px;
    height: 12px;
    margin-top: 4px;
    flex: none;
    fill: var(--ink-light);
  }
  .details .address { margin-bottom: 6px; }
</style>
</head>
<body>
<main class="canvas">

  <section class="card card-back" aria-label="Business card back">
    <span class="wordmark">Tovrin</span>
  </section>

  <section class="card card-front" aria-label="Business card front">
    <svg class="panels" viewBox="0 0 520 318" aria-hidden="true">
      <polygon class="panel-blue" points="0,0 296,0 344,318 0,318"/>
      <polygon class="panel-stripe" points="296,0 301,0 362,318 344,318"/>
    </svg>

    <div class="contact">
      <h1 class="name">Warren Halbeck</h1>
      <p class="role">General Manager</p>
      <ul class="details">
        <li class="address">
          <svg viewBox="0 0 12 12"><path d="M6 0a4 4 0 0 0-4 4c0 3 4 8 4 8s4-5 4-8a4 4 0 0 0-4-4zm0 5.6A1.6 1.6 0 1 1 6 2.4a1.6 1.6 0 0 1 0 3.2z"/></svg>
          <span>87 Marrow Ave,<br>Pendlebay, QLD, 4023</span>
        </li>
        <li>
          <svg viewBox="0 0 12 12"><path d="M2.4 0.5l2 2.2-1 1.3c.7 1.5 1.9 2.8 3.5 3.6l1.3-1 2.3 2-1 2.2C5 10.6 1.2 6.8.4 2z"/></svg>
          <span>0472 915 348</span>
        </li>
        <li>
          <svg viewBox="0 0 12 12"><path d="M0 2h12v8H0zM1 3v.4l5 3.3 5-3.3V3z"/></svg>
          <span>Warren.halbeck@tovrin.com.au</span>
        </li>
        <li>
          <svg viewBox="0 0 12 12"><path d="M6 0a6 6 0 1 0 0 12A6 6 0 0 0 6 0zm0 1.2c.7.8 1.2 2 1.4 3.3H4.6C4.8 3.2 5.3 2 6 1.2zM1.3 5.5h2.3c0 1.1.2 2.2.6 3.2A4.8 4.8 0 0 1 1.3 5.5zm3.3 0h2.8c0 1.2-.5 2.5-1.4 3.5-.9-1-1.4-2.3-1.4-3.5zm3.8 0h2.3a4.8 4.8 0 0 1-2.9 3.2c.4-1 .6-2.1.6-3.2z"/></svg>
          <span>www.tovrin.com.au</span>
        </li>
      </ul>
    </div>

    <span class="wordmark">Tovrin</span>
  </section>

</main>
</body>
</html>
```